Business card for Luxury Portable Restroom Trailer company

We are a Luxury Portable Restroom Trailer Company Called FALCRIDGE HIRES. Based in Orange County California. We provide portable restroom trailers for events, such as, Weddings, Concerts, Charity events, Sporting events, Tournaments, Corporate events, ect. We rent and Sell the Luxury restrooms. Our colors are white, grey, and Orange. As you will see in the logo we uploaded.
There are 2 people in the company so the names and titles will change for the 3 people but card will remain the same. Here is the information for each Person: Dwight Penner CFO 555 318-0476
next Person: Leon Marchetti VP 555 318-0476
Next Person: Owen Marchetti CEO 555 318-0476
Information to include on the card: Luxury Restroom Trailers Rental and Sales. Weddings, Concerts, Charity, Sporting and Corp. Events.

```html
<!DOCTYPE html>
<html lang="en">
<head>
<meta charset="utf-8">
<title>Falcridge Hires – Business Card</title>
<link href="https://fonts.googleapis.com/css2?family=Montserrat:wght@400;500;700;800&display=swap" rel="stylesheet">
<style>
  :root {
    --page-bg: #e4e4e4;
    --card-light: #636365;
    --card-dark: #4e4e50;
    --white: #ffffff;
    --orange: #ee6a24;
    --font: "Montserrat", Arial, sans-serif;
  }
  * { box-sizing: border-box; margin: 0; padding: 0; }
  html, body { width: 1200px; height: 1200px; overflow: hidden; }
  body {
    background: var(--page-bg);
    font-family: var(--font);
    color: var(--white);
    display: flex;
    flex-direction: column;
    align-items: center;
    justify-content: center;
    gap: 60px;
  }
  .card {
    position: relative;
    width: 860px;
    height: 491px;
    border-radius: 22px;
    background: linear-gradient(120deg, var(--card-light) 0%, var(--card-dark) 60%);
  }

  /* Front */
  .card-front {
    display: flex;
    flex-direction: column;
    align-items: center;
    justify-content: center;
    gap: 54px;
  }
  .brand-name {
    font-weight: 800;
    font-size: 74px;
    letter-spacing: 2px;
    color: var(--white);
    line-height: 1;
  }
  .services {
    text-align: center;
    font-weight: 500;
    font-size: 21px;
    line-height: 1.45;
    letter-spacing: 0.5px;
  }

  /* Back */
  .card-back .brand-mark {
    position: absolute;
    top: 48px;
    right: 56px;
    display: flex;
    align-items: center;
    gap: 12px;
  }
  .brand-mark .mark-circle {
    width: 46px;
    height: 46px;
    border: 4px solid var(--orange);
    border-radius: 50%;
  }
  .brand-mark .mark-name {
    font-weight: 700;
    font-size: 18px;
    letter-spacing: 1px;
    color: var(--white);
  }
  .contact-block {
    position: absolute;
    top: 178px;
    left: 0;
    right: 0;
    display: flex;
    justify-content: center;
    align-items: center;
    gap: 34px;
  }
  .person { text-align: right; }
  .person-name { font-weight: 700; font-size: 38px; line-height: 1.1; }
  .person-title { font-weight: 400; font-size: 24px; margin-top: 2px; }
  .divider { width: 3px; height: 118px; background: var(--orange); }
  .contact-list { list-style: none; display: flex; flex-direction: column; gap: 8px; }
  .contact-list li {
    display: flex;
    align-items: center;
    gap: 14px;
    font-size: 22px;
    font-weight: 500;
    letter-spacing: 0.5px;
  }
  .contact-list svg { width: 20px; height: 20px; flex: none; }
  .address {
    position: absolute;
    bottom: 70px;
    left: 0;
    right: 0;
    text-align: center;
    font-size: 22px;
    font-weight: 500;
    letter-spacing: 0.8px;
  }
</style>
</head>
<body>

  <section class="card card-front">
    <h1 class="brand-name">FALCRIDGE HIRES</h1>
    <p class="services">Luxury Restroom | Trailers Rental and Sales | Weddings |<br>Concerts | Charity | Sporting and Corp. Events</p>
  </section>

  <section class="card card-back">
    <div class="brand-mark">
      <span class="mark-circle"></span>
      <span class="mark-name">FALCRIDGE HIRES</span>
    </div>

    <div class="contact-block">
      <div class="person">
        <p class="person-name">Dwight Penner</p>
        <p class="person-title">CFO</p>
      </div>
      <span class="divider"></span>
      <ul class="contact-list">
        <li>
          <svg viewBox="0 0 24 24" fill="#ffffff" aria-hidden="true"><path d="M6.6 10.8a15.2 15.2 0 0 0 6.6 6.6l2.2-2.2a1 1 0 0 1 1-.25 11.4 11.4 0 0 0 3.6.57 1 1 0 0 1 1 1V20a1 1 0 0 1-1 1A17 17 0 0 1 3 4a1 1 0 0 1 1-1h3.5a1 1 0 0 1 1 1c0 1.25.2 2.45.57 3.57a1 1 0 0 1-.25 1z"/></svg>
          555 318-0476
        </li>
        <li>
          <svg viewBox="0 0 24 24" fill="#ffffff" aria-hidden="true"><path d="M2 5h20v14H2z M4 7v.5l8 5 8-5V7l-8 5z" fill-rule="evenodd"/></svg>
          info@falcridgehires.com
        </li>
        <li>
          <svg viewBox="0 0 24 24" fill="none" stroke="#ffffff" stroke-width="2" aria-hidden="true"><circle cx="12" cy="12" r="9"/><path d="M3 12h18M12 3c3 3 3 15 0 18M12 3c-3 3-3 15 0 18"/></svg>
          www.falcridgehires.com
        </li>
      </ul>
    </div>

    <p class="address">6148 Alder Crest Road Fenwick Maine 11408</p>
  </section>

</body>
</html>
```